Kampfsport Außenwerbung
Zielgruppe
Kampfsportschule für Kinder, Jugendliche und Erwachsene. Sportarten: Kick-Boxen, Jiu-Jitsu und Tricking
Aufgabenstellung
Ich bräuchte für meine Schaufenster eine schöne Außenwerbung. Beworben werden sollen alle meine Sportarten. Ich lade meinen Flyer hoch, damit im ähnlichen Stil gearbeitet werden kann. Außerdem auch noch andere Beispiele an denen man sich orientieren kann, sowie mein Logo und meine Fensterfront.

```html
<!DOCTYPE html>
<html lang="de">
<head>
<meta charset="utf-8">
<title>Martial Arts Borq – Außenwerbung</title>
<link rel="stylesheet" href="https://fonts.googleapis.com/css2?family=Russo+One&family=Syncopate:wght@700&family=Montserrat+Alternates:wght@600;700&display=swap">
<style>
  :root {
    --stage: #b1b1b1;
    --black: #000000;
    --red: #ec1c24;
    --red-dark: #a82226;
    --white: #ffffff;
    --ink: #111111;
  }
  html, body {
    margin: 0;
    width: 1200px;
    height: 1200px;
    overflow: hidden;
    background: var(--stage);
  }
  .banner {
    position: absolute;
    left: 366px;
    top: 70px;
    width: 466px;
    height: 1060px;
    display: block;
  }
  .headline { font-family: "Russo One", sans-serif; fill: var(--white); }
  .display { font-family: "Syncopate", sans-serif; font-weight: 700; }
  .body { font-family: "Montserrat Alternates", sans-serif; font-weight: 700; }
  .brand-name { font-family: "Montserrat Alternates", sans-serif; font-weight: 700; fill: var(--white); }
  .discipline { fill: var(--ink); font-size: 25px; }
</style>
</head>
<body>
<svg class="banner" viewBox="0 0 582 1325" xmlns="http://www.w3.org/2000/svg">
  <defs>
    <radialGradient id="glow-top" cx="0.5" cy="0.5" r="0.5">
      <stop offset="0" stop-color="#ffffff" stop-opacity="0.9"/>
      <stop offset="0.35" stop-color="#8a8a8a" stop-opacity="0.6"/>
      <stop offset="1" stop-color="#000000" stop-opacity="0"/>
    </radialGradient>
    <radialGradient id="glow-bottom" cx="0.5" cy="0.5" r="0.5">
      <stop offset="0" stop-color="#ffffff"/>
      <stop offset="0.3" stop-color="#9a9a9a" stop-opacity="0.7"/>
      <stop offset="1" stop-color="#000000" stop-opacity="0"/>
    </radialGradient>
    <linearGradient id="photo-tone" x1="0" y1="0" x2="0" y2="1">
      <stop offset="0" stop-color="#2a2a2a"/>
      <stop offset="0.45" stop-color="#e9e6ea"/>
      <stop offset="1" stop-color="#d8d4da"/>
    </linearGradient>
  </defs>

  <!-- top black section -->
  <rect class="top-field" x="0" y="0" width="582" height="600" fill="var(--black)"/>
  <ellipse cx="170" cy="300" rx="150" ry="160" fill="url(#glow-top)"/>

  <!-- corner stripes -->
  <polygon points="0,0 40,0 280,235 230,235" fill="var(--red-dark)"/>
  <polygon points="0,30 0,90 150,240 215,240" fill="var(--red)"/>

  <!-- headline bands -->
  <polygon points="0,311 582,136 582,319 0,488" fill="var(--red)"/>
  <polygon points="0,488 382,383 382,488 0,599" fill="var(--red-dark)"/>

  <!-- photo area -->
  <rect class="hero-photo" role="img" aria-label="Foto: Kind im weißen Karateanzug mit gelbem Gürtel in Kampfhaltung"
        x="382" y="40" width="200" height="533" fill="url(#photo-tone)"/>

  <polygon points="482,0 582,0 532,73" fill="var(--red)"/>

  <!-- brand name -->
  <text class="brand-name" x="292" y="152" font-size="22" text-anchor="middle">Martial Arts Borq</text>

  <!-- headline -->
  <g transform="rotate(-16.5 27 388)">
    <text class="headline" x="27" y="388" font-size="50" letter-spacing="3" textLength="290" lengthAdjust="spacingAndGlyphs">MARTIAL</text>
    <text class="headline" x="33" y="444" font-size="50" letter-spacing="3" textLength="340" lengthAdjust="spacingAndGlyphs">ARTS BORQ</text>
  </g>
  <g transform="rotate(-16.5 32 524)">
    <text class="headline" x="32" y="524" font-size="32" textLength="280" lengthAdjust="spacingAndGlyphs">WIR MACHEN</text>
    <text class="headline" x="46" y="564" font-size="32" textLength="330" lengthAdjust="spacingAndGlyphs">KINDER SICHER</text>
  </g>

  <!-- disciplines -->
  <rect x="0" y="573" width="582" height="752" fill="var(--white)"/>
  <polygon points="0,599 382,488 382,573 0,573" fill="var(--red-dark)"/>
  <polygon points="382,488 382,573 0,599" fill="var(--red-dark)" opacity="0"/>
  <polygon points="0,573 382,573 0,599" fill="var(--red-dark)" opacity="0"/>

  <text class="display" x="50" y="661" font-size="46" fill="var(--red)" textLength="470" lengthAdjust="spacingAndGlyphs">DISZIPLINEN:</text>
  <g class="discipline-list body">
    <polygon points="50,697 66,697 58,706" fill="var(--red)"/>
    <text class="discipline" x="70" y="707" textLength="405" lengthAdjust="spacingAndGlyphs">Kick-Boxen/Sportkarate</text>
    <polygon points="50,733 66,733 58,742" fill="var(--red)"/>
    <text class="discipline" x="70" y="743" textLength="462" lengthAdjust="spacingAndGlyphs">Jiu-Jitsu Selbstverteidigung</text>
    <polygon points="50,763 66,763 58,772" fill="var(--red)"/>
    <text class="discipline" x="70" y="778" textLength="128" lengthAdjust="spacingAndGlyphs">Tricking</text>
    <polygon points="50,799 66,799 58,808" fill="var(--red)"/>
    <text class="discipline" x="70" y="814" textLength="265" lengthAdjust="spacingAndGlyphs">U25 Kick-Boxen</text>
  </g>

  <!-- slogan band -->
  <polygon points="0,809 582,926 582,1325 0,1325" fill="var(--red-dark)"/>
  <polygon points="0,838 582,958 582,1325 0,1325" fill="var(--red)"/>
  <polygon points="0,963 582,1091 582,1325 0,1325" fill="var(--black)"/>
  <ellipse cx="272" cy="1030" rx="170" ry="95" fill="url(#glow-bottom)"/>
  <g transform="rotate(12 62 878)">
    <text class="headline" x="62" y="878" font-size="46" textLength="400" lengthAdjust="spacingAndGlyphs">WIR MACHEN</text>
    <text class="headline" x="42" y="934" font-size="46" textLength="474" lengthAdjust="spacingAndGlyphs">KINDER STARK!</text>
  </g>

  <!-- contact -->
  <g class="contact">
    <text class="display" x="77" y="1095" font-size="25" fill="var(--white)" textLength="418" lengthAdjust="spacingAndGlyphs">LEITUNG: TIMO BORQ</text>
    <text class="body" x="77" y="1127" font-size="18" fill="var(--white)" font-weight="600" textLength="427" lengthAdjust="spacingAndGlyphs">Am Werkhof 4c | 26500 Hornbachtal</text>
    <text class="display" x="77" y="1169" font-size="16" fill="var(--white)" textLength="382" lengthAdjust="spacingAndGlyphs">INFO &amp; PROBETRAINING:</text>

    <g class="icon-phone" fill="none" stroke="var(--white)" stroke-width="2.4">
      <circle cx="95" cy="1199" r="15"/>
      <path d="M89 1192 q-2 6 4 12 q6 6 12 4 l-3 -4 l-3 1 q-4 -2 -6 -6 l1 -3 z" fill="var(--white)" stroke="none"/>
    </g>
    <text class="body" x="134" y="1210" font-size="27" fill="var(--white)" textLength="255" lengthAdjust="spacingAndGlyphs">0151/ 2233 4455</text>

    <g class="icon-mail" fill="none" stroke="var(--white)" stroke-width="2.2">
      <rect x="80" y="1233" width="31" height="21"/>
      <path d="M80 1233 l15.5 12 l15.5 -12 M80 1254 l11 -10 M111 1254 l-11 -10"/>
    </g>
    <text class="body" x="134" y="1252" font-size="24" fill="var(--white)" textLength="356" lengthAdjust="spacingAndGlyphs">info@martial-arts-borq.de</text>
  </g>

  <!-- footer corners -->
  <polygon points="0,1225 74,1275 0,1325" fill="var(--red)"/>
  <polygon points="582,1222 506,1275 582,1325" fill="var(--red)"/>
</svg>
</body>
</html>
```